Stationery Design Project for Nimbora, Chicago

Nimbora, a street parking application which helps car drivers find a street parking spot by offering an ideal path along which to look for parking. This path is calculated by our algorithm based on data (e.g. historical data, baseball games schedule, etc.). Along this path the driver will find a spot and will also save 70% of the search time. Customer we target is reg. between 21 and 45 yo.

We envision something young, fresh, bright and original. Slightly abstract maybe. It should represent the idea and elements of finding street parking in the city, e.g. car(s), parking spot, people, city, etc. (just ideas!).

Logo is attached.

Requirement:
- Business Cards (2 Sided Full Color CMYK)
- Letterhead (1 Sided Full Color CMYK)
- Envelope (1 Sided Full Color CMYK)
- Sticker (1 Sided Full Color CMYK), round with a 2inch diameter.

Reason: We're starting to get more and more designs and need more time to look into all of them. Very exciting!! Thanks to everybody!

Hi all, we're in the process of selecting our favs. Though choices!!! Really good submissions. Will keep you posted and sorry for the delay.

Target Market(s)

Car drivers and owners between 21 and 45

Industry/Entity Type

Parking

Requirements
Must have
• Sticker should be round and include company URL nimbora.com and the new logo which we will attach soon.
Should not have
• Should not be too serious or boring.

```html
<!DOCTYPE html>
<html lang="en">
<head>
<meta charset="utf-8">
<title>Nimbora — Business Card</title>
<link href="https://fonts.googleapis.com/css2?family=PT+Sans:wght@400;700&display=swap" rel="stylesheet">
<style>
  :root {
    --brand-blue: #1f78be;
    --ink: #231f20;
    --muted: #555555;
    --card: #ffffff;
    --backdrop: #ecebe8;
    --rule: #c9c9c9;
    --photo-top: #d9dbdd;
    --photo-mid: #8d9196;
    --photo-low: #5c6066;
  }
  * { box-sizing: border-box; margin: 0; padding: 0; }
  html, body { width: 1200px; height: 758px; overflow: hidden; }
  body {
    background: var(--backdrop);
    font-family: "PT Sans", sans-serif;
    color: var(--ink);
    position: relative;
  }
  .card {
    position: absolute;
    top: 204px;
    width: 520px;
    height: 300px;
    background: var(--card);
    border-radius: 22px;
    box-shadow: 0 6px 18px rgba(0,0,0,0.18);
    overflow: hidden;
  }
  .card--front { left: 50px; }
  .card--back { left: 630px; }

  /* front */
  .brand {
    position: absolute;
    left: 40px;
    top: 92px;
    display: flex;
    align-items: center;
    gap: 12px;
  }
  .brand__dot {
    width: 58px; height: 58px;
    border-radius: 50%;
    background: var(--brand-blue);
  }
  .brand__name {
    font-size: 40px;
    font-weight: 700;
    color: var(--ink);
    letter-spacing: 0.5px;
  }
  .divider {
    position: absolute;
    left: 312px; top: 50px;
    width: 1px; height: 120px;
    background: var(--rule);
  }
  .contact {
    position: absolute;
    left: 326px; top: 48px;
  }
  .contact__name {
    font-size: 19px; font-weight: 700;
    color: var(--brand-blue);
    line-height: 1.1;
  }
  .contact__title {
    font-size: 13px; color: var(--muted);
    margin-bottom: 10px;
  }
  .contact__list { list-style: none; }
  .contact__item {
    display: flex; align-items: center; gap: 6px;
    font-size: 13px; color: var(--muted);
    line-height: 17px;
  }
  .contact__item svg { width: 10px; height: 10px; fill: var(--muted); flex: none; }
  .band {
    position: absolute;
    left: 0; top: 202px;
    width: 100%; height: 34px;
    background: var(--brand-blue);
  }
  .band__badge {
    position: absolute;
    left: 408px; top: 182px;
    width: 56px; height: 56px;
    border-radius: 50%;
    background: var(--brand-blue);
    border: 5px solid var(--card);
    box-shadow: 0 0 0 1px var(--rule);
  }
  .address {
    position: absolute;
    left: 0; right: 0; top: 250px;
    text-align: center;
    font-size: 13px;
    color: var(--muted);
  }

  /* back */
  .mark {
    position: absolute;
    left: 40px; top: 60px;
    width: 170px; height: 170px;
    border-radius: 50%;
    background: var(--brand-blue);
    box-shadow: 0 0 0 6px var(--card), 0 0 0 8px var(--rule);
    display: flex; align-items: center; justify-content: center;
  }
  .mark__name {
    font-size: 28px; font-weight: 700;
    color: var(--card);
  }
  .street-photo {
    position: absolute;
    left: 262px; top: 78px;
    width: 232px; height: 150px;
    border-radius: 4px;
    background: linear-gradient(160deg, var(--photo-top) 0%, var(--photo-mid) 55%, var(--photo-low) 100%);
  }
</style>
</head>
<body>
  <section class="card card--front" aria-label="Business card front">
    <div class="brand">
      <span class="brand__dot"></span>
      <span class="brand__name">Nimbora</span>
    </div>
    <div class="divider"></div>
    <div class="contact">
      <p class="contact__name">Your Name</p>
      <p class="contact__title">Title</p>
      <ul class="contact__list">
        <li class="contact__item">
          <svg viewBox="0 0 10 10"><path d="M2 0.5 L3.6 0.5 L4.2 2.8 L3 3.6 Q4 5.8 6.4 7 L7.2 5.8 L9.5 6.4 L9.5 8 Q9.5 9.5 8 9.5 Q0.5 9 0.5 2 Q0.5 0.5 2 0.5Z"/></svg>
          123-456-789
        </li>
        <li class="contact__item">
          <svg viewBox="0 0 10 10"><rect x="2.5" y="0.5" width="5" height="9" rx="1"/><rect x="3.3" y="1.6" width="3.4" height="5.4" fill="#fff"/></svg>
          123-456-789
        </li>
        <li class="contact__item">
          <svg viewBox="0 0 10 10"><rect x="0.5" y="2" width="9" height="6.5"/><path d="M0.8 2.3 L5 5.6 L9.2 2.3" stroke="#fff" stroke-width="0.8" fill="none"/></svg>
          hello@nimbora.com
        </li>
        <li class="contact__item">
          <svg viewBox="0 0 10 10"><circle cx="5" cy="5" r="4.5"/><path d="M0.5 5 H9.5 M5 0.5 Q2.5 5 5 9.5 M5 0.5 Q7.5 5 5 9.5" stroke="#fff" stroke-width="0.6" fill="none"/></svg>
          www.nimbora.com
        </li>
      </ul>
    </div>
    <div class="band"></div>
    <div class="band__badge"></div>
    <p class="address">Complex name, Street name, City, State, zip code</p>
  </section>

  <section class="card card--back" aria-label="Business card back">
    <div class="mark"><span class="mark__name">Nimbora</span></div>
    <div class="street-photo" role="img" aria-label="Overhead photo of cars parked in marked bays along a city street"></div>
  </section>
</body>
</html>
```